Template Flyer- Corewell Stretch & Flow

I am wanting a template 1 page flyer designed to use on the back ground of newsletter (faded background) and for our advertising posters in A4, A3, for Facebook and Instagram compatibility.

I have loaded an example from another Studio called Pinegrove (file 3)- each time they have a new workshop to advertise a picture is placed in the little circle (so this is something I would want to do too where I can load a new picture each time a new workshop is running)- They have used the flyer like a water mark...I like this.

Our colour palette is what is on our logos and you can also visit our website for a feel for what we like www.corewellstretch.com.au

I need some of the designs edited a bit more and because of the time difference, there seems to be a 24hour period where we communicate with each other. May I please request another 2 days extension

Requirements
Must have
• Id like to have a picture in the back ground. My favourite back ground that has been produced so far is a background of both picture file 9 and 10 in either.
Nice to have
• 3 picture circles options to advertise the events/workshops I have each year.
• Brush stroke style circles (see picture attached)rather then smooth circles for the picture area (in a grey tone)
Should not have
• No BLACK colour writing or black circles

```html
<!DOCTYPE html>
<html lang="en">
<head>
<meta charset="utf-8">
<title>Yoga &amp; Pilates Workshop Flyer</title>
<link href="https://fonts.googleapis.com/css2?family=Quicksand:wght@500;700&family=Source+Sans+3:wght@400;600;700&display=swap" rel="stylesheet">
<style>
  :root {
    --teal: #1b8fae;
    --ink: #4a5058;
    --soft-ink: #5b6168;
    --stage: #ffffff;
    --wash-top: #f3f3f1;
    --wash-mid: #dedcd6;
    --wash-low: #cfccc4;
    --brush-dark: #5e5f63;
    --brush-taupe: #b8b1a6;
    --panel: #ffffff;
  }
  * { margin: 0; padding: 0; box-sizing: border-box; }
  html, body { width: 960px; height: 1200px; overflow: hidden; background: var(--stage); }
  .flyer {
    position: absolute; left: 56px; top: 0; width: 848px; height: 1200px; overflow: hidden;
    font-family: "Source Sans 3", sans-serif; color: var(--ink);
  }
  .backdrop {
    position: absolute; inset: 0;
    background:
      radial-gradient(ellipse 40% 30% at 15% 45%, rgba(170,180,150,.35), transparent 70%),
      radial-gradient(ellipse 35% 40% at 88% 40%, rgba(150,165,140,.35), transparent 70%),
      radial-gradient(ellipse 30% 25% at 85% 90%, rgba(160,130,110,.3), transparent 70%),
      linear-gradient(180deg, var(--wash-top) 0%, var(--wash-top) 12%, var(--wash-mid) 45%, var(--wash-low) 100%);
  }
  .brand {
    position: absolute; top: 62px; left: 0; width: 100%;
    display: flex; justify-content: center; align-items: center; gap: 12px;
  }
  .brand-dot { width: 44px; height: 44px; border-radius: 50%; background: var(--teal); }
  .brand-name { font-weight: 400; font-size: 34px; color: var(--soft-ink); }
  .title {
    position: absolute; top: 154px; left: 0; width: 100%; text-align: center;
    font-family: "Quicksand", sans-serif; font-weight: 700; color: var(--teal);
    font-size: 47px; line-height: 47px;
  }
  .photo-ring { position: absolute; left: 180px; top: 256px; width: 490px; height: 490px; }
  .details { position: absolute; left: 0; width: 100%; text-align: center; font-weight: 700; }
  .date { top: 775px; font-size: 31px; line-height: 38px; color: var(--teal); }
  .date sup { font-size: 18px; }
  .time { top: 821px; font-size: 24px; line-height: 26px; }
  .venue { top: 860px; font-size: 23px; line-height: 25px; }
  .invest-label { top: 920px; font-size: 30px; line-height: 34px; color: var(--teal); letter-spacing: .5px; }
  .prices { top: 963px; font-size: 24px; line-height: 25px; }
  .cta { top: 1022px; font-size: 31px; line-height: 38px; color: var(--teal); }
  .writeup {
    position: absolute; left: 38px; top: 1069px; width: 773px; height: 104px;
    background: var(--panel); display: flex; align-items: center; justify-content: center;
    font-size: 20px; color: var(--soft-ink);
  }
</style>
</head>
<body>
<main class="flyer">
  <div class="backdrop" role="img" aria-label="Faded background photo of the studio entrance garden with planter box and white picket fence"></div>

  <header class="brand">
    <span class="brand-dot"></span>
    <span class="brand-name">Corewell Stretch &amp; Flow</span>
  </header>

  <h1 class="title">YOGA &amp; PILATES<br>Workshop, Woodend</h1>

  <svg class="photo-ring" viewBox="0 0 490 490">
    <defs>
      <linearGradient id="studioTones" x1="0" y1="0" x2="1" y2="1">
        <stop offset="0" stop-color="#e9e7e3"/>
        <stop offset=".5" stop-color="#8a8580"/>
        <stop offset=".8" stop-color="#b49c7c"/>
        <stop offset="1" stop-color="#a8b58a"/>
      </linearGradient>
    </defs>
    <circle cx="245" cy="245" r="226" fill="url(#studioTones)" role="img" aria-label="Workshop photo: yoga mats with cork blocks and patterned bolsters"/>
    <path d="M250 12 A233 233 0 0 0 250 478" fill="none" stroke="var(--brush-dark)" stroke-width="9" stroke-linecap="round"/>
    <path d="M250 6 A239 239 0 0 1 370 450" fill="none" stroke="var(--brush-taupe)" stroke-width="7" stroke-linecap="round"/>
    <path d="M430 330 A233 233 0 0 1 290 470" fill="none" stroke="var(--brush-dark)" stroke-width="5" stroke-linecap="round"/>
  </svg>

  <p class="details date">Saturday 24<sup>th</sup> March 2018</p>
  <p class="details time">10.00am - 4.00pm</p>
  <p class="details venue">Corewell Stretch and Flow<br>18 Larch Street Woodend</p>
  <p class="details invest-label">INVESTMENT</p>
  <p class="details prices">$120.00<br>$100.00 concession</p>
  <p class="details cta">Book early&nbsp; Places are limited.</p>

  <section class="writeup">write up about the event/workshop</section>
</main>
</body>
</html>
```